Request for Business Card Design

Hi. My name is Marlene, I am looking for a new business card design for my company, Quarrow Signal Instruments, LLC. I really like the design you did for Tarsel Venture and was hoping you could do something similar using our full logo and our mark. I am also open to any raised texture design using our mark. I have attached our full logo, which would need to be somewhere on the card, as well as the mark in both outline and full form, as well as our brand colors / guide. The card does not have to be white, as long as our logo and mark appear. I actually like darker colored business cards more, but am open to all options. If you are interested in working with me, please let me know. We would also take the business card design into letterhead design if you can do that.

```html
<!DOCTYPE html>
<html lang="en">
<head>
<meta charset="utf-8">
<title>Quarrow Signal Instruments – Business Card</title>
<link rel="stylesheet" href="https://fonts.googleapis.com/css2?family=Open+Sans:wght@400;700;800&display=swap">
<style>
  :root {
    --backdrop: #232324;
    --card: #3f3f41;
    --card-ink: #1c1c1d;
    --accent: #1597c7;
    --text: #ffffff;
    --font: "Open Sans", Arial, sans-serif;
  }
  * { box-sizing: border-box; margin: 0; padding: 0; }
  html, body {
    width: 1200px; height: 780px; overflow: hidden;
    background: var(--backdrop);
    font-family: var(--font);
  }
  .canvas { position: relative; width: 1200px; height: 780px; }
  .card {
    position: absolute;
    width: 540px; height: 310px;
    background: var(--card);
    border-bottom: 5px solid var(--accent);
  }
  .card--front { left: 60px; top: 60px; }
  .card--back { left: 600px; top: 410px; }

  /* Front */
  .brand {
    position: absolute; left: 0; right: 0; top: 0; bottom: 0;
    display: flex; align-items: center; justify-content: center; gap: 16px;
  }
  .brand__dot {
    width: 46px; height: 46px; border-radius: 50%;
    background: var(--card-ink);
  }
  .brand__name {
    color: var(--card-ink);
    font-weight: 800; font-size: 24px; letter-spacing: 1px;
    line-height: 1.1; text-transform: uppercase;
  }

  /* Back */
  .person { position: absolute; left: 60px; top: 112px; text-align: right; width: 170px; }
  .person__name { color: var(--accent); font-weight: 800; font-size: 40px; line-height: 1; }
  .person__role { color: var(--text); font-size: 15px; margin-top: 2px; }
  .divider {
    position: absolute; left: 250px; top: 82px;
    width: 2px; height: 110px; background: var(--text);
  }
  .contacts { position: absolute; left: 272px; top: 86px; list-style: none; }
  .contacts li {
    display: flex; align-items: center; gap: 8px;
    color: var(--text); font-size: 13px; line-height: 24px;
  }
  .contacts svg { width: 13px; height: 13px; fill: var(--accent); flex: none; }
  .address {
    position: absolute; left: 0; right: 0; top: 248px;
    text-align: center; color: var(--text); font-size: 15px;
  }
</style>
</head>
<body>
<main class="canvas">
  <section class="card card--front" aria-label="Card front">
    <div class="brand">
      <span class="brand__dot"></span>
      <span class="brand__name">Quarrow Signal<br>Instruments</span>
    </div>
  </section>

  <section class="card card--back" aria-label="Card back">
    <div class="person">
      <p class="person__name">Marlene</p>
      <p class="person__role">Director</p>
    </div>
    <span class="divider"></span>
    <ul class="contacts">
      <li><svg viewBox="0 0 16 16"><path d="M3 1l3 3-2 2c1 2 3 4 6 6l2-2 3 3-2 2C7 15 1 9 1 3z"/></svg>+001 555 210 4830</li>
      <li><svg viewBox="0 0 16 16"><path d="M4 1h7v4H4zM1 6h14v9H1zm3 3v2h2V9zm4 0v2h2V9z"/></svg>+001 555 210 4831</li>
      <li><svg viewBox="0 0 16 16"><circle cx="8" cy="8" r="7"/></svg>www.quarrowsignal.com</li>
      <li><svg viewBox="0 0 16 16"><path d="M1 3h14v10H1zm1 1l6 5 6-5z"/></svg>info@quarrowsignal.com</li>
    </ul>
    <p class="address">1180 Harbor Mill Road • Fenwick, CO 80999</p>
  </section>
</main>
</body>
</html>
```